Small Business Broker Business Card Design

A business card design for a small business brokerage, which is a financial service, not unlike real estate brokerage, but for small businesses such as laundromats, pizza shops, restaurants, cleaners etc. The designs should all be simple, more conservative in nature, using the colors and font of the logo. Again, think real estate Brokerage as a business context
Contact Information for Business Card
Name: Glen R. Harlow. Title: Small Business Advisor. Email: g.harlow@bayfieldcapitalworks.example. Mobile: (555) 274-3918. Office: (555) 806-2147. www.bayfieldcapitalworks.example

```html
<!DOCTYPE html>
<html lang="en">
<head>
<meta charset="utf-8">
<title>Bayfield Capital Works – Business Card</title>
<link rel="stylesheet" href="https://fonts.googleapis.com/css2?family=Montserrat:wght@700&family=Arimo:ital,wght@0,400;0,700;1,400&display=swap">
<style>
  :root {
    --navy: #173060;
    --green: #7dc242;
    --white: #ffffff;
    --ink: #5a5a5a;
    --backdrop: #1c1c1e;
  }
  * { box-sizing: border-box; margin: 0; padding: 0; }
  html, body { width: 1200px; height: 963px; overflow: hidden; background: var(--backdrop); }
  .stage { position: relative; width: 1200px; height: 963px; }
  .card {
    position: absolute; left: 240px; width: 720px; height: 411px;
    border-radius: 26px; overflow: hidden;
    box-shadow: 0 10px 30px rgba(0,0,0,.45);
  }
  .card--front { top: 48px; background: var(--white); }
  .card--back { top: 504px; background: var(--navy); }

  .front__band { position: absolute; left: 0; top: 0; width: 100%; height: 122px; background: var(--navy); }
  .front__stripe { position: absolute; left: 0; top: 122px; width: 100%; height: 12px; background: var(--green); }
  .holder { position: absolute; left: 46px; top: 34px; color: var(--white); }
  .holder__name { font: 700 25px/1.1 "Montserrat", sans-serif; letter-spacing: 1.5px; text-transform: uppercase; }
  .holder__title { font: italic 400 15px/1.3 "Arimo", sans-serif; margin-top: 4px; }

  .brand { position: absolute; right: 44px; top: 190px; text-align: right; }
  .brand__name { font: 400 20px/1.2 "Arimo", sans-serif; color: var(--navy); }
  .brand__tagline { font: 400 12px/1.4 "Arimo", sans-serif; color: var(--ink); margin-top: 4px; }

  .contacts { position: absolute; left: 46px; top: 250px; list-style: none; }
  .contacts li { display: flex; align-items: center; gap: 12px; font: 400 17px/1.55 "Arimo", sans-serif; color: var(--ink); }
  .contacts svg { width: 16px; height: 16px; flex: none; }

  .back__brand { position: absolute; left: 0; right: 0; top: 168px; text-align: center; color: var(--white); }
  .back__name { font: 400 30px/1.2 "Arimo", sans-serif; }
  .back__tagline { font: 400 15px/1.4 "Arimo", sans-serif; margin-top: 10px; opacity: .85; }
</style>
</head>
<body>
<main class="stage">
  <section class="card card--front" aria-label="Business card front">
    <div class="front__band"></div>
    <div class="front__stripe"></div>
    <div class="holder">
      <h1 class="holder__name">Glen R. Harlow</h1>
      <p class="holder__title">Small Business Advisor</p>
    </div>
    <div class="brand">
      <p class="brand__name">Bayfield Capital Works, Inc</p>
      <p class="brand__tagline">Confidently buy or sell a local business today</p>
    </div>
    <ul class="contacts">
      <li>
        <svg viewBox="0 0 16 16" fill="none" stroke="#7dc242" stroke-width="1.6"><path d="M3 2h3l1.2 3-1.7 1.2a8 8 0 0 0 4.3 4.3L11 8.8l3 1.2v3c0 .6-.5 1-1 1A12 12 0 0 1 2 3c0-.5.4-1 1-1z"/></svg>
        (555) 806-2147
      </li>
      <li>
        <svg viewBox="0 0 16 16" fill="none" stroke="#7dc242" stroke-width="1.6"><rect x="4" y="1.5" width="8" height="13" rx="1.5"/><line x1="7" y1="12" x2="9" y2="12"/></svg>
        (555) 274-3918
      </li>
      <li>
        <svg viewBox="0 0 16 16" fill="none" stroke="#7dc242" stroke-width="1.6"><rect x="1.5" y="3.5" width="13" height="9" rx="1"/><path d="M1.5 4l6.5 5 6.5-5"/></svg>
        g.harlow@bayfieldcapitalworks.example
      </li>
      <li>
        <svg viewBox="0 0 16 16" fill="none" stroke="#7dc242" stroke-width="1.4"><circle cx="8" cy="8" r="6.5"/><ellipse cx="8" cy="8" rx="3" ry="6.5"/><line x1="1.5" y1="8" x2="14.5" y2="8"/></svg>
        www.bayfieldcapitalworks.example
      </li>
    </ul>
  </section>

  <section class="card card--back" aria-label="Business card back">
    <div class="back__brand">
      <p class="back__name">Bayfield Capital Works, Inc</p>
      <p class="back__tagline">Confidently buy or sell a local business today</p>
    </div>
  </section>
</main>
</body>
</html>
```